Coastal Learner Bureau business cards

Australian company about to start offering its services. We recruit international students to come to study English, vocational education and postgraduate courses in Australia. We help them find the institution and select the right city they want to come to Australia. We are a young, online oriented and supportive agency. Our clients are between 18 and 35 years old, mainly University students, young professionals or people with work experience. We provide much more information that any other agency offer. We administrate a Facebook group with more than 11.000 members that daily ask questions about general information when coming to Australia, while they are here and even after they leave the country

Target Market(s)

International students from South America, Central America and Europe

Industry/Entity Type

Student

Contact Information for Business Card

Tomas Bilbrea
Managing Director
tomas@kelvarin.com.au
www.kelvoria.com.au
+61 491058264
Melbourne, Australia

Font styles to use
Serif
Sans Serif

Colors

Designer to choose colors to be used in the design.

Requirements
Must have
• Horizontal design
• Standard business card size and shape. If font uses green or yellow colours, they will have to match the ones from the logo
Nice to have
• UPDATE: Use the contents of the green image to design one of the card sides. Use our logo in the background of that side as watermark.
• Passport image, or immigration stamps. A picture of the Yarra River (from Melbourne) would be cool as well.
Should not have
• Non-standard business card size and shape
• Not black as the background colour of any sides as we are not a VIP agency or a hight class service. We are orientes to young people and they like colours, pictures, something attractive.
• Vertical design
• NO YELLOW or BLACK AS THE BACKGROUND COLOUR OF ANY SIDE OF THE BIZ CARD

```html
<!DOCTYPE html>
<html lang="en">
<head>
<meta charset="utf-8">
<title>Kelvoria business cards</title>
<link href="https://fonts.googleapis.com/css2?family=Roboto:wght@400;500;700&family=Roboto+Condensed:wght@700&family=Open+Sans:ital,wght@1,700&display=swap" rel="stylesheet">
<style>
  :root {
    --backdrop: #e9e6e1;
    --card-white: #fbfbfa;
    --brand-green: #1d6b3c;
    --brand-yellow: #e9c21c;
    --text-grey: #4a4a4a;
    --sky-top: #6f9fd4;
    --sky-mid: #bcd2e6;
    --city-mid: #6f8a8c;
    --water: #3d6f9a;
    --white: #ffffff;
  }
  * { margin: 0; padding: 0; box-sizing: border-box; }
  html, body { width: 1200px; height: 960px; overflow: hidden; }
  body {
    background: var(--backdrop);
    font-family: "Roboto", Arial, sans-serif;
    position: relative;
  }
  .card {
    position: absolute;
    width: 600px;
    height: 344px;
    border-radius: 20px;
    overflow: hidden;
    box-shadow: 0 3px 6px rgba(0,0,0,0.18);
  }
  .card-front { left: 302px; top: 128px; background: var(--card-white); }
  .card-back { left: 299px; top: 488px; }

  .brand-mark {
    position: absolute;
    left: 44px;
    top: 84px;
    display: flex;
    align-items: center;
    gap: 10px;
  }
  .brand-dot {
    width: 16px; height: 16px; border-radius: 50%;
    background: var(--brand-yellow);
  }
  .brand-name {
    font-family: "Roboto", Arial, sans-serif;
    font-weight: 700;
    font-size: 40px;
    color: var(--brand-green);
    letter-spacing: 0.5px;
  }

  .person { position: absolute; left: 44px; top: 242px; }
  .person-name {
    font-family: "Roboto Condensed", "Arial Narrow", sans-serif;
    font-weight: 700;
    font-size: 21px;
    color: var(--brand-green);
    line-height: 24px;
  }
  .person-title {
    font-family: "Roboto", Arial, sans-serif;
    font-weight: 500;
    font-size: 15.5px;
    color: var(--brand-yellow);
    line-height: 20px;
    letter-spacing: 0.2px;
  }
  .contact-line {
    display: flex;
    align-items: center;
    gap: 6px;
    font-size: 14.5px;
    color: var(--text-grey);
    line-height: 19px;
  }
  .contact-line svg { width: 12px; height: 12px; fill: var(--brand-green); flex: none; }
  .person .contact-line { margin-top: 2px; }
  .contacts { position: absolute; left: 379px; top: 246px; }

  .city-photo {
    position: absolute; inset: 0;
    background: linear-gradient(180deg, var(--sky-top) 0%, var(--sky-mid) 30%, var(--city-mid) 58%, var(--water) 80%, #2e5a80 100%);
  }
  .back-brand {
    position: absolute;
    left: 0; right: 0; top: 140px;
    text-align: center;
    font-weight: 700;
    font-size: 52px;
    color: var(--white);
  }
  .tagline {
    position: absolute;
    left: 0; right: 0; top: 294px;
    display: flex;
    justify-content: center;
    align-items: center;
    gap: 6px;
  }
  .tagline-rule { width: 48px; height: 1px; background: var(--white); opacity: 0.8; }
  .tagline-text {
    font-family: "Open Sans", Arial, sans-serif;
    font-style: italic;
    font-weight: 700;
    font-size: 15px;
    color: var(--white);
  }
</style>
</head>
<body>
  <section class="card card-front">
    <div class="brand-mark">
      <span class="brand-dot"></span>
      <span class="brand-name">Kelvoria</span>
    </div>

    <div class="person">
      <div class="person-name">TOMAS BILBREA</div>
      <div class="person-title">MANAGING DIRECTOR</div>
      <div class="contact-line">
        <svg viewBox="0 0 12 12"><path d="M6 0C3.6 0 2 1.7 2 4c0 3 4 8 4 8s4-5 4-8c0-2.3-1.6-4-4-4zm0 5.6A1.6 1.6 0 1 1 6 2.4a1.6 1.6 0 0 1 0 3.2z"/></svg>
        <span>Melbourne, Australia</span>
      </div>
    </div>

    <div class="contacts">
      <div class="contact-line">
        <svg viewBox="0 0 12 12"><path d="M2.4 0.6l2 2-1 1.4c.7 1.6 2 2.9 3.6 3.6l1.4-1 2 2-1.2 2.2C4.6 10.6 1.4 7.4.2 1.8z"/></svg>
        <span>+61 491058264</span>
      </div>
      <div class="contact-line">
        <svg viewBox="0 0 12 12"><path d="M0 2h12v1L6 7 0 3zM0 4.3l6 4 6-4V10H0z"/></svg>
        <span>tomas@kelvarin.com.au</span>
      </div>
      <div class="contact-line">
        <svg viewBox="0 0 12 12"><circle cx="6" cy="6" r="6"/><path d="M1 6h10M6 1c-2 2.5-2 7.5 0 10M6 1c2 2.5 2 7.5 0 10" stroke="#fff" stroke-width="0.9" fill="none"/></svg>
        <span>www.kelvoria.com.au</span>
      </div>
    </div>
  </section>

  <section class="card card-back">
    <div class="city-photo" role="img" aria-label="Photograph of the Yarra River in Melbourne with city towers, trees and a bright sun in a blue sky"></div>
    <div class="back-brand">Kelvoria</div>
    <div class="tagline">
      <span class="tagline-rule"></span>
      <span class="tagline-text">Hacemos más por ti!</span>
      <span class="tagline-rule"></span>
    </div>
  </section>
</body>
</html>
```